Redesign of business card for Cedar Ridge Mechanical

We are looking for a new design for our business cards for Cedar Ridge Mechanical. We are a plumbing & HVAC construction company, operating on the West Coast of Canada and USA. Logo attached.
Industry/Entity Type
Construction - Plumbing & HVAC
Contact Information for Business Card
Name, address, phone numbers, email, website address
Look and feel
Each slider illustrates characteristics of the customer's brand and the style your logo design should communicate.

```html
<!DOCTYPE html>
<html lang="en">
<head>
<meta charset="utf-8">
<title>Cedar Ridge Mechanical – Business Card</title>
<link rel="stylesheet" href="https://fonts.googleapis.com/css2?family=Montserrat:wght@400;500;600;700&display=swap">
<style>
  :root {
    --backdrop: #e7e3dd;
    --card-light: #ffffff;
    --card-dark: #262626;
    --ink: #1f1f1f;
    --ink-soft: #2b2b2b;
    --paper-text: #ffffff;
  }
  * { margin: 0; padding: 0; box-sizing: border-box; }
  html, body {
    width: 900px; height: 1200px; overflow: hidden;
    background: var(--backdrop);
    font-family: "Montserrat", sans-serif;
    color: var(--ink);
  }
  .stage { position: relative; width: 900px; height: 1200px; }

  .card {
    position: absolute;
    border-radius: 22px;
    overflow: hidden;
    box-shadow: 0 6px 14px rgba(0,0,0,0.25);
  }
  .card-front { left: 80px; top: 131px; width: 742px; height: 441px; background: var(--card-light); }
  .card-back { left: 78px; top: 640px; width: 744px; height: 438px; background: var(--card-dark); }

  .brand-name {
    position: absolute;
    font-weight: 600;
    line-height: 1.15;
    text-align: center;
  }
  .card-front .brand-name {
    left: 110px; top: 190px; width: 236px;
    font-size: 22px; color: var(--ink);
  }
  .card-back .brand-name {
    left: 0; width: 744px; top: 182px;
    font-size: 40px; color: var(--paper-text);
  }

  .divider {
    position: absolute; left: 356px; top: 154px;
    width: 2px; height: 149px; background: var(--ink);
  }

  .person { position: absolute; left: 375px; top: 152px; }
  .person-name { font-size: 25px; font-weight: 700; color: var(--ink); line-height: 1.2; }
  .person-title { font-size: 15.5px; font-weight: 500; color: var(--ink-soft); margin-top: 2px; }

  .contact-list { position: absolute; left: 375px; top: 224px; list-style: none; }
  .contact-item {
    display: flex; align-items: center; gap: 10px;
    height: 30px; font-size: 15.5px; font-weight: 500; color: var(--ink);
  }
  .contact-item svg { width: 15px; height: 15px; flex: none; fill: var(--ink); }

  .address-band {
    position: absolute; left: 0; top: 371px; width: 742px; height: 35px;
    background: var(--ink-soft);
    color: var(--paper-text);
    font-size: 15.5px; font-weight: 400;
    display: flex; align-items: center; justify-content: center;
  }
</style>
</head>
<body>
<main class="stage">
  <section class="card card-front" aria-label="Card front">
    <p class="brand-name">Cedar Ridge<br>Mechanical</p>
    <div class="divider"></div>
    <div class="person">
      <h1 class="person-name">Daniel Brooks</h1>
      <p class="person-title">Managing Director</p>
    </div>
    <ul class="contact-list">
      <li class="contact-item">
        <svg viewBox="0 0 24 24" aria-hidden="true"><path d="M6.6 10.8a15.1 15.1 0 0 0 6.6 6.6l2.2-2.2a1 1 0 0 1 1-.25 11.4 11.4 0 0 0 3.6.57 1 1 0 0 1 1 1V20a1 1 0 0 1-1 1A17 17 0 0 1 3 4a1 1 0 0 1 1-1h3.5a1 1 0 0 1 1 1c0 1.25.2 2.45.57 3.57a1 1 0 0 1-.25 1z"/></svg>
        555.214.7730
      </li>
      <li class="contact-item">
        <svg viewBox="0 0 24 24" aria-hidden="true"><path d="M3 5h18v14H3z M3 5l9 7 9-7" fill="none" stroke="#1f1f1f" stroke-width="0"/><path d="M2 5.5h20v1.2l-10 6.6-10-6.6z M2 8.8l10 6.6 10-6.6V19H2z"/></svg>
        info@cedarridgemechanical.com
      </li>
      <li class="contact-item">
        <svg viewBox="0 0 24 24" aria-hidden="true"><circle cx="12" cy="12" r="9" fill="none" stroke="#1f1f1f" stroke-width="2"/><path d="M12 3v18M3 12h18" stroke="#1f1f1f" stroke-width="1.6"/><ellipse cx="12" cy="12" rx="4" ry="9" fill="none" stroke="#1f1f1f" stroke-width="1.6"/></svg>
        www.cedarridgemechanical.com
      </li>
    </ul>
    <div class="address-band">48 Harbor Pine Road Fairview, OR 97024</div>
  </section>

  <section class="card card-back" aria-label="Card back">
    <p class="brand-name">Cedar Ridge<br>Mechanical</p>
  </section>
</main>
</body>
</html>
```